Anesthesia Medical Practice Business Card

We need a business card to hand out to surgeons with my basic information. Something that stands out but is not over the top. The medical community is rather conservative. I'd like them to call me first when flipping through their rolodex of anesthesiologists. I'd like the card to communicate confidence, control, professionalism yet serenity. I don't want the card to be pricey to print.

he logo will be provided as a vector graphic in addition to a complete business card design including the logo

Lem Varo Keshtel, M.D.
Board Certified Anesthesiologist

(555) 386-2157

lkeshtel@quorvanmail.example

Mailing Address:
47315 Brindlecove Ave.
Suite 382-6475
Los Angeles, CA 90877

A logo that inegrates my initials perhaps
LK MD
My initials are LK and MD as in Medical Doctor

or
perhaps a physician in surgical mask and cap caring for a patient

Target Market(s)

Surgeons who need anesthesia services

Industry/Entity Type

Medical

Requirements
Must have
• the logo will be provided as a vector graphic in addition to a complete business card design including the logo

Lem Varo Keshtel, M.D.

(555) 386-2157

lkeshtel@quorvanmail.example

Mailing Address:
47315 Brindlecove Ave.
Suite 382-6475
Los Angeles, CA 90877

Nice to have
• A logo that inegrates my initials perhaps
LK MD

or

```html
<!DOCTYPE html>
<html lang="en">
<head>
<meta charset="UTF-8">
<title>Lem Varo Keshtel, M.D. — Business Card</title>
<link rel="stylesheet" href="https://fonts.googleapis.com/css2?family=Josefin+Sans:wght@300;400;600&display=swap">
<style>
  :root {
    --page-bg: #3b322d;
    --card-center: #ffffff;
    --card-edge: #a9a9a9;
    --ink: #1a1a1a;
    --ink-soft: #3c3c3c;
    --mark: #111111;
  }
  * { margin: 0; padding: 0; box-sizing: border-box; }
  html, body {
    width: 1200px;
    height: 1000px;
    overflow: hidden;
    background: var(--page-bg);
  }
  .canvas {
    width: 1200px;
    height: 1000px;
    display: flex;
    align-items: center;
    justify-content: center;
  }
  .business-card {
    width: 840px;
    height: 480px;
    border-radius: 4px;
    background: radial-gradient(ellipse 60% 62% at 50% 45%, var(--card-center) 0%, #f1f1f1 45%, var(--card-edge) 100%);
    display: flex;
    flex-direction: column;
    align-items: center;
    justify-content: center;
    font-family: "Josefin Sans", sans-serif;
    color: var(--ink);
    text-align: center;
  }
  .brand {
    display: flex;
    align-items: center;
    gap: 14px;
    margin-bottom: 22px;
  }
  .brand-dot { display: block; }
  .brand-name {
    font-size: 40px;
    font-weight: 300;
    letter-spacing: 2px;
    color: var(--mark);
    line-height: 1;
  }
  .doctor-name {
    font-size: 25px;
    font-weight: 400;
    letter-spacing: 1.5px;
  }
  .doctor-title {
    font-size: 15px;
    font-weight: 300;
    letter-spacing: 1px;
    color: var(--ink-soft);
    margin-top: 4px;
  }
  .contact {
    margin-top: 22px;
    font-size: 15px;
    font-weight: 300;
    line-height: 1.45;
    color: var(--ink-soft);
  }
  .address {
    margin-top: 14px;
    font-size: 15px;
    font-weight: 300;
    line-height: 1.4;
    color: var(--ink-soft);
    font-style: normal;
  }
</style>
</head>
<body>
  <main class="canvas">
    <section class="business-card">
      <div class="brand">
        <svg class="brand-dot" width="40" height="40" viewBox="0 0 40 40" aria-hidden="true">
          <circle cx="20" cy="20" r="20" fill="#111111"/>
        </svg>
        <span class="brand-name">LK</span>
      </div>
      <h1 class="doctor-name">Lem Varo Keshtel, M.D.</h1>
      <p class="doctor-title">Board Certified Anesthesiologist</p>
      <div class="contact">
        <p class="phone">(555) 386-2157</p>
        <p class="email">lkeshtel@quorvanmail.example</p>
      </div>
      <address class="address">
        Mailing Address:<br>
        47315 Brindlecove Ave.<br>
        Suite 382-6475<br>
        Los Angeles, CA 90877
      </address>
    </section>
  </main>
</body>
</html>
```